Brightway Carpet and Tile cleaning Business card Design

I need a design that has the same feel as my van.
i would also like a prominent "Review us on Friendlink" somewhere, but not that it makes it look silly.
I would like the card to have a little bit of grey or black in the design as well.

It will need contact details
phone: 0455 817264
email: rkbrightwayclean@mailbox-example.com
website: www.brightwaycarpetandtilecleaning-example.com.au
Friendlink: /brightwaycarpetandtilecleaning

Industry/Entity Type

Business

Contact Information for Business Card

Phone number 0455817264
Email rkbrightwayclean@mailbox-example.com
Website www.brightwaycarpetandtilecleaning-example.com.au
Facebook/brightwaycarpetandtilecleaning

Colors
000000

Requirements
Must have
• Same feel as my van
• I want the card to stand out from the crowd
Nice to have
• Maybe include a tiny bit of a third colour? Grey's,blacks, orange?

```html
<!DOCTYPE html>
<html lang="en">
<head>
<meta charset="utf-8">
<title>Brightway Carpet and Tile Cleaning – Business Card</title>
<link rel="stylesheet" href="https://fonts.googleapis.com/css2?family=Open+Sans:ital,wght@0,400;0,700;1,400&display=swap">
<style>
  :root {
    --page-bg: #e7e4e2;
    --card-bg: #f3f1f1;
    --brand-blue: #1db4e1;
    --ink-grey: #4a4d52;
    --white: #ffffff;
  }
  * { margin: 0; padding: 0; box-sizing: border-box; }
  html, body {
    width: 1200px;
    height: 900px;
    overflow: hidden;
    background: var(--page-bg);
    font-family: "Open Sans", Arial, sans-serif;
  }
  .business-card {
    position: absolute;
    left: 120px;
    top: 153px;
    width: 960px;
    height: 594px;
    background: var(--card-bg);
    overflow: hidden;
    box-shadow: 0 8px 30px rgba(0,0,0,0.15);
  }
  .card-diagonal {
    position: absolute;
    inset: 0;
  }
  .brand-mark {
    position: absolute;
    left: 60px;
    top: 118px;
    display: flex;
    align-items: center;
    gap: 18px;
  }
  .brand-dot {
    width: 40px;
    height: 40px;
    border-radius: 50%;
    background: var(--brand-blue);
    flex: none;
  }
  .brand-name {
    color: var(--ink-grey);
    font-weight: 700;
    font-size: 33px;
    line-height: 1.2;
  }
  .contact-list {
    position: absolute;
    right: 58px;
    top: 310px;
    list-style: none;
    color: var(--white);
    font-size: 21px;
    text-align: right;
  }
  .contact-item {
    display: flex;
    justify-content: flex-end;
    align-items: center;
    gap: 20px;
    height: 40px;
  }
  .contact-icon {
    width: 20px;
    height: 20px;
    flex: none;
  }
  .review-callout {
    position: absolute;
    right: 60px;
    top: 496px;
    color: var(--white);
    font-style: italic;
    font-size: 28px;
  }
</style>
</head>
<body>
  <div class="business-card">
    <svg class="card-diagonal" width="960" height="594" viewBox="0 0 960 594" aria-hidden="true">
      <polygon points="0,594 960,0 960,594" fill="var(--brand-blue)"/>
    </svg>

    <div class="brand-mark">
      <span class="brand-dot"></span>
      <span class="brand-name">Brightway<br>Carpet &amp; Tile Cleaning</span>
    </div>

    <ul class="contact-list">
      <li class="contact-item">
        <span>0455 817264</span>
        <svg class="contact-icon" viewBox="0 0 20 20" aria-hidden="true">
          <path d="M4 2l3 0 1.5 4-2 1.5c1 2 2.5 3.5 4.5 4.5l1.5-2 4 1.5 0 3c0 1-1 2-2 2C8 16.5 3.5 12 3 4c0-1 .5-2 1-2z" fill="var(--white)"/>
        </svg>
      </li>
      <li class="contact-item">
        <span>rkbrightwayclean@mailbox-example.com</span>
        <svg class="contact-icon" viewBox="0 0 20 20" aria-hidden="true">
          <rect x="2" y="5" width="16" height="11" fill="var(--white)"/>
          <path d="M2 5l8 6 8-6" fill="none" stroke="var(--brand-blue)" stroke-width="1.4"/>
        </svg>
      </li>
      <li class="contact-item">
        <span>www.brightwaycarpetandtilecleaning-example.com.au</span>
        <svg class="contact-icon" viewBox="0 0 20 20" aria-hidden="true">
          <circle cx="10" cy="10" r="8" fill="var(--white)"/>
          <path d="M2 10h16M10 2c-3 3-3 13 0 16M10 2c3 3 3 13 0 16" fill="none" stroke="var(--brand-blue)" stroke-width="1.2"/>
        </svg>
      </li>
      <li class="contact-item">
        <span>/brightwaycarpetandtilecleaning</span>
        <svg class="contact-icon" viewBox="0 0 20 20" aria-hidden="true">
          <rect x="2" y="2" width="16" height="16" rx="2" fill="var(--white)"/>
        </svg>
      </li>
    </ul>

    <p class="review-callout">Review us on Friendlink</p>
  </div>
</body>
</html>
```